Social Media Cover and Profile

We already have our own logo. We just need a fresh design on our social media pages. We are not happy with our current designs. We would like to incorporate our ZING billboard and the colors are blue (#05143f) and white. You can also incorporate silver as well. We are a family law office (Divorce and Custody) We no longer want to incorporate the Capital of Harrisburg photo that we are currently using. You can look at our Facebook page; The Law Office of Milo T. Brennick.

Target Market(s)

Potential Clients

Industry/Entity Type

Family Law

Logo Text

Our Logo Is The Law Office of Milo T. Brennick with the Sheild

Requirements
Must have
• Text to include:
Central Pennslyvania's Premier Family Law Firm

Ability to be resized to and used as all images in social media, including but not limited to: Youtube Channel art, Facebook Cover and Profile.
Nice to have
• Darker color but we are open to "bright" ideas.

```html
<!DOCTYPE html>
<html lang="en">
<head>
<meta charset="UTF-8">
<title>ZING – Social Cover</title>
<link href="https://fonts.googleapis.com/css2?family=Playfair+Display:wght@700&family=Roboto:wght@700&display=swap" rel="stylesheet">
<style>
  :root {
    --page-bg: #f2f2f2;
    --card-bg: #ececec;
    --card-glow: #ffffff;
    --navy: #05143f;
    --silver-light: #e4e4e4;
    --silver-mid: #a9a9a9;
    --silver-dark: #7d7d7d;
  }
  html, body {
    margin: 0;
    padding: 0;
    width: 1200px;
    height: 720px;
    overflow: hidden;
    background: var(--page-bg);
  }
  .canvas {
    position: relative;
    width: 1200px;
    height: 720px;
  }
  .cover {
    position: absolute;
    left: 51px;
    top: 152px;
    width: 1102px;
    height: 420px;
    background: var(--card-bg);
    box-shadow: 4px 8px 10px rgba(0,0,0,0.35);
    overflow: hidden;
  }
  .cover__bokeh {
    position: absolute;
    inset: 0;
    background:
      radial-gradient(ellipse 45% 70% at 70% 35%, var(--card-glow) 0%, rgba(255,255,255,0) 70%),
      radial-gradient(ellipse 30% 50% at 25% 55%, rgba(255,255,255,0.6) 0%, rgba(255,255,255,0) 70%),
      linear-gradient(180deg, #e6e6e6 0%, #f0f0f0 60%, #ebebeb 100%);
  }
  .cover__headline {
    position: absolute;
    left: 0;
    top: 0;
    width: 1102px;
    height: 420px;
  }
  .cover__headline text {
    font-family: "Roboto", Arial, sans-serif;
    font-weight: 700;
  }
  .cover__tagline {
    position: absolute;
    left: 0;
    right: 0;
    top: 306px;
    margin: 0;
    text-align: center;
    font-family: "Playfair Display", Georgia, serif;
    font-weight: 700;
    font-size: 31px;
    color: var(--navy);
    letter-spacing: 0.1px;
  }
</style>
</head>
<body>
  <div class="canvas">
    <section class="cover">
      <div class="cover__bokeh" role="img" aria-label="Soft silver bokeh light background"></div>
      <svg class="cover__headline" viewBox="0 0 1102 420" aria-label="ZING">
        <defs>
          <linearGradient id="silver" x1="0" y1="0" x2="1" y2="0">
            <stop offset="0" stop-color="var(--silver-mid)"/>
            <stop offset="0.25" stop-color="var(--silver-light)"/>
            <stop offset="0.5" stop-color="var(--silver-dark)"/>
            <stop offset="0.75" stop-color="var(--silver-light)"/>
            <stop offset="1" stop-color="var(--silver-mid)"/>
          </linearGradient>
        </defs>
        <text x="551" y="283" text-anchor="middle" font-size="236" fill="url(#silver)" textLength="690" lengthAdjust="spacingAndGlyphs">ZING</text>
      </svg>
      <p class="cover__tagline">Central Pennslyvania's Premier Family Law Firm</p>
    </section>
  </div>
</body>
</html>
```